Bring me business with this creative business card

Design my new business card. I am looking for something different with an impact. People will take a look at this card & they will 1- see how different & creative I am, 2-understand what I do 3- Call me to meet me!

I make videos with a message, testimonials. I am dynamic, fun, creative & human. My new website is in construction but in the meantime you can check this old one: brightpath.ca & another one Tidebloom.com & tidebloom facebook page.
I make videos. sometimes with a cameraman, sometimes with my phone. As an ex Public Relations agent, the message is the most important thing for me. I want to make my clients shine! When they start with me they often remind me of a lamb, when I finish coaching them they are powerful like LIONS! That's why I need a powerful business card!

Target Market(s)

Entrepreneurs, solo entrepreneurs, small & medium companies & start ups. People i will meet while networking. People that need videos on their website & social Networks to get attention, to be visible. men & women. From 35 to 49 years old.
I am an ex Public relations agent. I used to send clients in traditional medias, now with videos they have more chances to be seen on google the new media. I do videos of the president, his team, his loyal clients saying how great the company is & expert videos like series so people can be seen for example every 1 st of every month with a short 2 minute video. Also with my 20 years in marketing & communications I can coach & give tips to anybody who needs it.
Target: anybody who would like my old website brightpath.ca & I also have another website but it will be off line soon: tidebloom.com could give you ideas.

Industry/Entity Type

Communications

Contact Information for Business Card

I am in Montreal,So the business cards have to be the usual size like we have in Montreal: 9 cm x 5 cm
Details:My text: Mathilde Tessier Communication coach/CHIEF STORYTELLER. "Making videos as bold as you are" off: 514-555-0147 cell: 514-555-0183. tidebloom.com
mathilde@tidebloom.com logo facebook, youtube, instagram

Colors
f37122

Requirements
Must have
• Dynamic, happy. Orange. Be creative in the look but NOT the shape of the card. Easy to read. Big enough to read.
Should not have
• No funny shapes: no round, no square, just the usual. I love creative but NOT on shape.

```html
<!DOCTYPE html>
<html lang="en">
<head>
<meta charset="UTF-8">
<title>Tidebloom Business Card</title>
<link rel="stylesheet" href="https://fonts.googleapis.com/css2?family=Cinzel:wght@500&family=Roboto:wght@400;500&display=swap">
<style>
  :root {
    --backdrop: #e9e4dd;
    --card-white: #f7f7f7;
    --card-dark: #1c1e1e;
    --orange: #f37122;
    --orange-deep: #ef5a24;
    --amber: #f7a21b;
    --yellow: #ffd21a;
    --text-light: #ffffff;
  }
  * { box-sizing: border-box; margin: 0; padding: 0; }
  html, body { width: 1200px; height: 960px; overflow: hidden; }
  body {
    background: var(--backdrop);
    position: relative;
    font-family: "Roboto", Arial, sans-serif;
  }
  .card {
    position: absolute;
    left: 320px;
    width: 600px;
    height: 342px;
    overflow: hidden;
  }
  /* Front */
  .card-front { top: 100px; background: var(--card-white); }
  .front-mark {
    position: absolute; left: 252px; top: 70px; width: 103px; height: 128px;
    background: linear-gradient(180deg, var(--orange) 0%, var(--amber) 45%, var(--yellow) 70%, var(--orange) 100%);
    clip-path: polygon(12% 0, 88% 0, 100% 25%, 100% 72%, 72% 100%, 28% 100%, 0 72%, 0 25%);
  }
  .wordmark {
    position: absolute; left: 0; right: 0; top: 204px; text-align: center;
    font-family: "Cinzel", Georgia, serif; font-weight: 500;
    font-size: 34px; letter-spacing: 1px; color: var(--orange); line-height: 1;
  }
  .motto {
    position: absolute; left: 0; right: 0; top: 243px;
    display: flex; align-items: center; justify-content: center; gap: 8px;
    font-size: 14px; letter-spacing: 0.5px; color: var(--amber);
  }
  .motto::before, .motto::after {
    content: ""; width: 30px; height: 1.5px; background: var(--amber);
  }
  .slogan {
    position: absolute; left: 0; right: 0; top: 263px; text-align: center;
    font-size: 14px; font-weight: 500; color: var(--orange);
  }
  .social-row {
    position: absolute; left: 0; right: 0; top: 305px;
    display: flex; align-items: center; justify-content: center; gap: 4px;
  }
  .social-row .rule { width: 88px; height: 1px; background: linear-gradient(90deg, transparent, var(--orange)); }
  .social-row .rule.right { background: linear-gradient(90deg, var(--orange), transparent); }
  .social-dot { width: 22px; height: 22px; border-radius: 50%; background: var(--orange-deep); }
  /* Back */
  .card-back { top: 493px; background: var(--card-white); }
  .back-panel {
    position: absolute; left: 0; top: 0; width: 460px; height: 100%;
    background: var(--card-dark);
  }
  .back-art {
    position: absolute; left: 315px; top: 0; width: 283px; height: 342px;
    background: linear-gradient(180deg, var(--orange) 0%, var(--amber) 35%, var(--yellow) 62%, var(--orange) 100%);
    clip-path: polygon(10% 9%, 35% 0, 65% 0, 90% 9%, 97% 28%, 100% 55%, 82% 92%, 50% 100%, 18% 92%, 0 55%, 3% 28%);
  }
  .identity { position: absolute; left: 31px; top: 24px; }
  .identity .name { font-size: 22px; font-weight: 500; color: var(--orange-deep); letter-spacing: 0.3px; }
  .identity .role { font-size: 15px; font-weight: 500; color: var(--amber); line-height: 19px; margin-top: 4px; }
  .contacts { position: absolute; left: 33px; top: 244px; list-style: none; }
  .contacts li {
    display: flex; align-items: center; gap: 8px;
    font-size: 14px; color: var(--text-light); height: 19.5px;
  }
  .contacts svg { width: 13px; height: 13px; fill: var(--orange-deep); flex: none; }
</style>
</head>
<body>
  <section class="card card-front">
    <div class="front-mark" role="img" aria-label="Faceted low-poly lion head illustration in orange and yellow"></div>
    <div class="wordmark">TIDEBLOOM</div>
    <div class="motto">1 STORY &nbsp;1 VOICE</div>
    <div class="slogan">Making videos as bold as you are</div>
    <div class="social-row">
      <span class="rule"></span>
      <span class="social-dot"></span>
      <span class="social-dot"></span>
      <span class="social-dot"></span>
      <span class="rule right"></span>
    </div>
  </section>

  <section class="card card-back">
    <div class="back-panel"></div>
    <div class="back-art" role="img" aria-label="Large faceted low-poly lion head illustration in orange and yellow"></div>
    <div class="identity">
      <div class="name">MATHILDE T.</div>
      <div class="role">COMMUNICATION COACH<br>CHIEF STORYTELLER</div>
    </div>
    <ul class="contacts">
      <li><svg viewBox="0 0 16 16"><path d="M3.5 1l2.5 3-1.5 2c1 2 3 4 5 5l2-1.5 3 2.5-1.5 2.5C7 15 1 9 1 2.5z"/></svg>514-555-0147</li>
      <li><svg viewBox="0 0 16 16"><path d="M4 0h8a1 1 0 0 1 1 1v14a1 1 0 0 1-1 1H4a1 1 0 0 1-1-1V1a1 1 0 0 1 1-1zm1 2v10h6V2zm3 11a1 1 0 1 0 0 2 1 1 0 0 0 0-2z"/></svg>514-555-0183.</li>
      <li><svg viewBox="0 0 16 16"><path d="M1 3h14v1L8 9 1 4zm0 3l7 5 7-5v7H1z"/></svg>mathilde@tidebloom.com</li>
      <li><svg viewBox="0 0 16 16"><path d="M8 1a7 7 0 1 0 0 14A7 7 0 0 0 8 1zm-1 2.5c-.5 1-2 1.5-2 3s2 1 2 2.5-1 2-1 3.5C3.5 11.5 3 9 3 8c0-2.5 2-4.3 4-4.5zm2.5.2c2 .6 3.5 2.3 3.5 4.3 0 1-.3 2-1 3-.5-1-1.5-1.5-2.5-1.5S9 8.5 9.5 7c.3-1 1.5-1 1-2z"/></svg>www.tidebloom.com</li>
    </ul>
  </section>
</body>
</html>
```